boosters

revamp current booster flyer - modernize make it look better

please use website
Kowhaibaygroup.co.nz for as much as possible

i want you all to come with own wording description etc

```html
<!DOCTYPE html>
<html lang="en">
<head>
<meta charset="utf-8">
<title>Kowhai Bay Auto Centre – Brake &amp; Clutch Boosters</title>
<link rel="stylesheet" href="https://fonts.googleapis.com/css2?family=Poppins:wght@400;500;600;700;800&display=swap">
<style>
:root{
  --yellow:#ffd400;
  --ink:#1b1b1b;
  --charcoal:#3a3a3c;
  --night:#161718;
  --white:#ffffff;
  --page:#e9eaec;
  --red:#e8344a;
}
*{margin:0;padding:0;box-sizing:border-box}
html,body{width:1200px;height:2439px;overflow:hidden;background:var(--page);font-family:'Poppins',sans-serif}
.flyer{position:absolute;left:14px;top:460px;width:977px;height:1265px;background:var(--white);transform:scale(1.2);transform-origin:0 0;overflow:hidden;box-shadow:0 6px 24px rgba(0,0,0,.18)}
.abs{position:absolute}
.hero{left:0;top:0;width:977px;height:497px;background:radial-gradient(ellipse at 30% 35%,#2e3034 0%,#1a1b1d 55%,var(--night) 100%)}
.hero-part{left:455px;top:30px;width:480px;height:440px;border-radius:14px;background:linear-gradient(135deg,rgba(214,184,20,.55) 0%,rgba(150,150,154,.45) 45%,rgba(70,71,74,.35) 100%)}
.brand{left:60px;top:120px;display:flex;align-items:center;gap:14px}
.brand-mark{width:34px;height:34px;background:var(--yellow)}
.brand-name{color:var(--white);font-weight:700;font-size:30px;line-height:1.1;letter-spacing:1px}
.headline{left:50px;top:278px;font-weight:800;font-size:62px;line-height:57px;letter-spacing:-.5px}
.headline .hl{color:var(--yellow);display:block}
.headline .wt{color:var(--white);display:block}
.band{left:0;top:478px;width:528px;height:62px;background:var(--yellow);border-radius:0 22px 22px 0;clip-path:polygon(0 0,100% 0,96% 100%,0 100%)}
.band span{position:absolute;left:55px;top:15px;font-weight:700;font-size:22px;color:#1e1e1e}
.products{left:55px;top:552px;display:flex;gap:33px}
.product{width:137px;height:137px;border:3px solid #111;background:var(--white);display:flex;align-items:center;justify-content:center}
.product .shot{width:105px;height:90px;border-radius:10px;background:radial-gradient(circle at 45% 45%,#5b5c60 0%,#1d1d1f 60%,#111 100%)}
.product .shot.light{background:radial-gradient(circle at 45% 45%,#e4ddd2 0%,#a9a297 60%,#6d6861 100%)}
.company{left:55px;top:708px;font-weight:800;font-size:33px;color:var(--ink);letter-spacing:-.3px;white-space:nowrap}
.specialise{left:55px;top:780px;width:468px;height:82px;border:2px dashed #333}
.specialise .label{position:absolute;left:22px;top:-14px;background:var(--white);padding:0 12px;font-weight:600;font-size:17px;color:#2a2a2a}
.specialise .items{position:absolute;left:32px;top:24px;display:flex;gap:30px}
.item{display:flex;align-items:center;gap:10px;font-weight:600;font-size:15px;color:#333}
.dot{width:40px;height:40px;border-radius:50%;background:var(--yellow);display:flex;align-items:center;justify-content:center}
.aim{left:52px;top:888px;display:flex;align-items:center;gap:12px;font-weight:800;font-size:40px;color:var(--ink)}
.aim-text{left:54px;top:946px;font-size:22px;line-height:27px;color:#333}
.freephone{left:52px;top:1015px;display:flex;height:60px}
.freephone .tag{width:205px;background:var(--yellow);font-weight:800;font-size:28px;color:#111;display:flex;align-items:center;justify-content:center}
.freephone .num{width:268px;background:var(--charcoal);font-weight:700;font-size:30px;color:var(--white);display:flex;align-items:center;justify-content:center}
.services{left:565px;top:722px;width:412px;height:380px;background:var(--charcoal);clip-path:polygon(14px 0,100% 0,100% 100%,0 100%,0 14px)}
.svc-list{position:absolute;left:45px;top:30px;list-style:none}
.svc-list li{display:flex;align-items:center;gap:30px;height:60px}
.svc-list li span{font-weight:600;font-size:26px;color:var(--white);border-bottom:2px solid #5a5a5c;width:198px;padding-bottom:6px;white-space:nowrap}
.svc-note{position:absolute;left:40px;top:302px;font-weight:600;font-size:21px;line-height:28px;color:var(--yellow);white-space:nowrap}
.footer-shapes{left:0;top:1087px}
.contact-left{left:52px;top:1110px}
.contact-left p{display:flex;align-items:center;gap:12px;font-weight:700;font-size:28px;color:var(--white);line-height:40px}
.contact-left .unsub{font-weight:400;font-size:15px;color:var(--yellow);letter-spacing:1.5px;margin-top:4px}
.address{left:365px;top:1116px;display:flex;align-items:center;gap:14px;color:var(--white);white-space:nowrap}
.address strong{font-weight:500;font-size:22px}
.address span{font-weight:500;font-size:18px;display:flex;align-items:center;gap:8px}
.web{left:438px;top:1168px;font-size:21px;color:#1e1e1e;line-height:32px}
.web p{display:flex;align-items:center;gap:10px}
</style>
</head>
<body>
<main class="flyer">
  <div class="abs hero" role="img" aria-label="Dark workshop photo of a mechanic fitting a brake disc"></div>
  <div class="abs hero-part" role="img" aria-label="Photo of a yellow brake caliper mounted on a silver brake drum"></div>

  <div class="abs brand">
    <div class="brand-mark"></div>
    <div class="brand-name">KOWHAI BAY<br>AUTO CENTRE</div>
  </div>

  <h1 class="abs headline">
    <span class="hl">BRAKE &amp;</span>
    <span class="hl">CLUTCH</span>
    <span class="wt">BOOSTERS</span>
  </h1>

  <div class="abs band"><span>SUPPLIERS &amp; REPAIRERS OF BOOSTERS</span></div>

  <div class="abs products">
    <div class="product"><div class="shot" role="img" aria-label="Vacuum brake booster"></div></div>
    <div class="product"><div class="shot" role="img" aria-label="Clutch booster with valve"></div></div>
    <div class="product"><div class="shot light" role="img" aria-label="Master cylinders"></div></div>
    <div class="product"><div class="shot" role="img" aria-label="Remote brake booster"></div></div>
    <div class="product"><div class="shot" role="img" aria-label="Truck air booster"></div></div>
  </div>

  <h2 class="abs company">KOWHAI BAY AUTO CENTRE</h2>

  <div class="abs specialise">
    <div class="label">SPECIALISE IN THE RE-MANUFACTURE OF</div>
    <div class="items">
      <div class="item"><div class="dot"><svg width="22" height="22" viewBox="0 0 22 22"><circle cx="11" cy="11" r="9" fill="none" stroke="#1b1b1b" stroke-width="2.5"/><circle cx="11" cy="11" r="3" fill="#1b1b1b"/></svg></div>BRAKES</div>
      <div class="item"><div class="dot"><svg width="22" height="22" viewBox="0 0 22 22"><path d="M7 3v12h10" fill="none" stroke="#1b1b1b" stroke-width="2.5"/><rect x="4" y="16" width="14" height="3" fill="#1b1b1b"/></svg></div>HOSES</div>
      <div class="item"><div class="dot"><svg width="22" height="22" viewBox="0 0 22 22"><circle cx="11" cy="11" r="9" fill="none" stroke="#1b1b1b" stroke-width="2.5"/><rect x="8" y="6" width="6" height="8" rx="1" fill="#1b1b1b"/></svg></div>CABLES</div>
    </div>
  </div>

  <h2 class="abs aim"><svg width="42" height="42" viewBox="0 0 42 42"><circle cx="21" cy="21" r="18" fill="none" stroke="var(--red)" stroke-width="5"/><circle cx="21" cy="21" r="8" fill="none" stroke="var(--red)" stroke-width="4"/><path d="M21 21L37 5" stroke="#3a6fd8" stroke-width="3"/></svg>OUR AIM</h2>
  <p class="abs aim-text">is to repair parts with the quickest<br>turn-around times possible</p>

  <div class="abs freephone"><div class="tag">FREE PHONE</div><div class="num">0800 55 61 48</div></div>

  <section class="abs services">
    <ul class="svc-list">
      <li><svg width="30" height="30" viewBox="0 0 30 30"><rect x="2" y="8" width="17" height="13" fill="none" stroke="var(--yellow)" stroke-width="2.5"/><path d="M19 12h6l3 5v4h-9z" fill="var(--yellow)"/><circle cx="8" cy="24" r="3" fill="var(--yellow)"/><circle cx="23" cy="24" r="3" fill="var(--yellow)"/></svg><span>Truck Boosters</span></li>
      <li><svg width="30" height="30" viewBox="0 0 30 30"><circle cx="9" cy="21" r="6" fill="none" stroke="var(--yellow)" stroke-width="3"/><path d="M13 17L25 5" stroke="var(--yellow)" stroke-width="5"/></svg><span>Clutch Boosters</span></li>
      <li><svg width="30" height="30" viewBox="0 0 30 30"><rect x="4" y="3" width="7" height="24" fill="none" stroke="var(--yellow)" stroke-width="2.5"/><rect x="15" y="12" width="12" height="15" fill="none" stroke="var(--yellow)" stroke-width="2.5"/></svg><span>Vacuum Boosters</span></li>
      <li><svg width="30" height="30" viewBox="0 0 30 30"><rect x="3" y="9" width="13" height="18" rx="2" fill="none" stroke="var(--yellow)" stroke-width="2.5"/><circle cx="23" cy="20" r="5" fill="none" stroke="var(--yellow)" stroke-width="2.5"/><path d="M5 5q4-4 9 0" fill="none" stroke="var(--yellow)" stroke-width="2"/></svg><span>Remotes boosters</span></li>
    </ul>
    <p class="svc-note">Kowhai Bay Auto Centre can<br>also supply parts and kits etc</p>
  </section>

  <svg class="abs footer-shapes" width="977" height="178" viewBox="0 0 977 178" aria-hidden="true">
    <polygon points="0,0 312,0 380,178 0,178" fill="var(--charcoal)"/>
    <polygon points="335,13 977,13 977,70 355,70" fill="var(--charcoal)"/>
    <polygon points="355,70 977,70 977,178 392,178" fill="var(--yellow)"/>
  </svg>

  <div class="abs contact-left">
    <p><svg width="26" height="26" viewBox="0 0 24 24"><path d="M6.6 10.8a15 15 0 006.6 6.6l2.2-2.2c.3-.3.7-.4 1-.2 1.1.4 2.300.6 3.6.6.6 0 1 .4 1 1V20c0 .6-.4 1-1 1A17 17 0 013 4c0-.6.4-1 1-1h3.5c.6 0 1 .4 1 1 0 1.3.2 2.5.6 3.6.1.3 0 .7-.2 1z" fill="var(--yellow)"/></svg>07 839 2046</p>
    <p><svg width="26" height="26" viewBox="0 0 24 24"><rect x="6" y="2" width="12" height="6" fill="var(--yellow)"/><rect x="2" y="9" width="20" height="9" rx="2" fill="var(--yellow)"/><rect x="6" y="15" width="12" height="7" fill="var(--yellow)" stroke="var(--charcoal)" stroke-width="1.5"/></svg>07 839 2047</p>
    <p class="unsub">Unsubscribe from this list</p>
  </div>

  <div class="abs address">
    <strong>KOWHAI BAY AUTO CENTRE</strong>
    <span><svg width="16" height="20" viewBox="0 0 16 20"><path d="M8 1a6 6 0 00-6 6c0 4.5 6 11 6 11s6-6.5 6-11a6 6 0 00-6-6z" fill="none" stroke="var(--yellow)" stroke-width="2.2"/><circle cx="8" cy="7" r="2" fill="var(--yellow)"/></svg>18 Totara Street, Hamilton</span>
  </div>

  <div class="abs web">
    <p><svg width="18" height="18" viewBox="0 0 18 18"><circle cx="9" cy="9" r="7.5" fill="none" stroke="#333" stroke-width="1.6"/><path d="M1.5 9h15M9 1.5c3 3 3 12 0 15M9 1.5c-3 3-3 12 0 15" fill="none" stroke="#333" stroke-width="1.3"/></svg>parts@kowhaibaygroup.co.nz</p>
    <p><svg width="18" height="18" viewBox="0 0 18 18"><rect x="1.5" y="4" width="15" height="11" fill="none" stroke="#333" stroke-width="1.6"/><path d="M1.5 4l7.5 6 7.5-6" fill="none" stroke="#333" stroke-width="1.6"/></svg>www. kowhaibaygroup.co.nz</p>
  </div>
</main>
</body>
</html>
```